Flyer für Therapie- und Gesundheitsdienstleister
Immer wieder gern. Kann ich nur weiterempfehlen!
Zielgruppe
Therapie- und Gesundheitsdienstleister im Bereich Physiotherapie, Podologie, Prävention und betriebliche Gesundheitsförderung. Für dieses Projekt möchten wir einen Flyer erstellen lassen für die Bewerbung der betrieblichen Gesundheitsförderungen in bzw. für Firmen
Aufgabenstellung
Klare Strukturen, nicht verspielt, DINA4 oder DINA5; leicht medizinischer Touch, evntuell Stockfotos integrieren, edel und hochwertiges Design

```html
<!DOCTYPE html>
<html lang="de">
<head>
<meta charset="utf-8">
<title>Betriebliche Gesundheitsförderung – Flyer</title>
<link href="https://fonts.googleapis.com/css2?family=Gilda+Display&family=Open+Sans:wght@400;600;700&display=swap" rel="stylesheet">
<style>
  :root{
    --orange:#e97a22;
    --ink:#3c3c3c;
    --paper:#ffffff;
    --photo-warm-a:#f2b58a;
    --photo-warm-b:#d9dde0;
    --photo-sky-a:#c9c2bc;
    --photo-sky-b:#e9e2da;
  }
  *{box-sizing:border-box;margin:0;padding:0}
  html,body{width:1200px;height:849px;overflow:hidden;background:var(--paper)}
  body{font-family:"Open Sans",Arial,sans-serif;color:var(--ink);position:relative}
  .page{position:absolute;top:0;width:600px;height:849px;overflow:hidden;background:var(--paper)}
  .page--front{left:0}
  .page--inside{left:600px}
  .footer-band{position:absolute;left:0;right:0;bottom:0;height:15px;background:var(--orange)}

  /* front page */
  .brand{position:absolute;left:440px;top:30px;display:flex;align-items:center;gap:8px}
  .brand__dot{width:30px;height:30px;border-radius:50%;background:var(--orange)}
  .brand__name{font-size:14.5px;line-height:19px;color:#555}
  .front-band{position:absolute;left:0;top:227px;width:600px;height:227px;background:var(--orange)}
  .front-photo{position:absolute;left:19px;top:175px;width:417px;height:315px;
    border-radius:62px 0 62px 0;
    background:linear-gradient(135deg,var(--photo-warm-b) 0%,#c7d3cf 35%,var(--photo-warm-a) 70%,#f4e1d4 100%)}
  .front-title{position:absolute;left:17px;top:505px;font-family:"Gilda Display",Georgia,serif;font-weight:400;
    font-size:66px;line-height:66px;color:var(--orange);white-space:nowrap;
    transform:scaleX(0.82);transform-origin:left top}
  .front-lead{position:absolute;left:20px;top:663px;font-size:11.4px;line-height:14.5px;
    letter-spacing:-0.15px;white-space:nowrap}
  .front-contact{position:absolute;left:20px;top:734px;font-size:11.4px;line-height:14.5px;letter-spacing:-0.15px}
  .cta{position:absolute;left:400px;top:736px;width:152px;height:70px;
    border:2px solid var(--orange);border-radius:34px 0 34px 0;
    display:flex;align-items:center;justify-content:center;font-weight:700;font-size:11px}

  /* inside page */
  .inside-head{position:absolute;left:0;top:0;width:600px;height:202px;background:var(--orange)}
  .inside-photo{position:absolute;left:23px;top:22px;width:554px;height:151px;
    border-radius:120px 0 120px 0;
    background:linear-gradient(100deg,var(--photo-sky-a) 0%,var(--photo-sky-b) 40%,#f1d9c8 70%,#dcd7d3 100%)}
  .inside-title-tab{position:absolute;left:50px;top:137px;width:345px;height:38px;
    background:var(--orange);border-radius:36px 14px 0 0}
  .inside-title{position:absolute;left:81px;top:152px;font-family:"Gilda Display",Georgia,serif;font-weight:400;
    font-size:21px;color:#fff;white-space:nowrap;transform:scaleX(0.84);transform-origin:left top}

  .col{position:absolute;top:258px;font-size:10.8px;line-height:13.2px;letter-spacing:-0.12px;hyphens:manual}
  .col--1{left:23px;width:180px}
  .col--2{left:211px;width:178px}
  .col--3{left:400px;width:180px}
  .col p{margin-bottom:12px}
  .col b{font-weight:700}
  .tag{display:inline-block;background:var(--orange);color:#fff;font-weight:700;font-size:10px;
    line-height:13px;padding:4px 12px 4px 6px;border-radius:0 8px 0 8px;margin-bottom:14px}
  .tag--wide{display:block;padding:6px 6px;margin:6px 0 14px}
  .bullets{list-style:none;margin-bottom:12px}
  .bullets li{position:relative;padding-left:18px}
  .bullets li::before{content:"";position:absolute;left:2px;top:5px;width:3px;height:3px;border-radius:50%;background:#6aa33b}
  .plain-list{list-style:none}
</style>
</head>
<body>

<section class="page page--front">
  <div class="brand">
    <span class="brand__dot"></span>
    <span class="brand__name">Zentrum<br>Vitalwerk</span>
  </div>
  <div class="front-band"></div>
  <div class="front-photo" role="img" aria-label="Foto: lächelnde Trainerin mit Brille im Fitnessraum an Ausdauergeräten"></div>
  <h1 class="front-title">Betriebliche<br>Gesundheitsförderung</h1>
  <p class="front-lead">Die betriebliche Gesundheitsförderung hat das Ziel die Gesundheit der Mitarbeiter zu erhalten<br>und zu fördern sowie die Leistungsfähigkeit und Motivation der Belegschaft zu steigern.</p>
  <p class="front-contact">Nehmen Sie gerne unverbindlich Kontakt zu uns auf:<br>www.vitalwerk-firmen.de</p>
  <div class="cta">Wir unterstützen Sie!</div>
  <div class="footer-band"></div>
</section>

<section class="page page--inside">
  <div class="inside-head"></div>
  <div class="inside-photo" role="img" aria-label="Foto: Gruppe beim Dehnen im Freien mit erhobenen Armen"></div>
  <div class="inside-title-tab"></div>
  <h2 class="inside-title">Betriebliche Gesundheitsförderung</h2>

  <div class="col col--1">
    <p style="margin-bottom:6px">Immer mehr gewinnen folgende Punkte an Bedeutung für Unter&shy;nehmen:</p>
    <div class="tag tag--wide">1) Mitarbeiterbindung<br>2) Arbeitgeber-Attraktivität erhöhen, um einen Vorteil am Bewerbermarkt zu erziehlen</div>
    <p>Auch da können wir Sie mit <b>unse&shy;rem Know-How</b> und <b>abgerunde&shy;ten Konzept</b> unterstützen.</p>
    <p>In regelmäßigen Abständen set&shy;zen wir uns mit Ihren Mitarbeitern in Verbindung und erfragen den jeweiligen IST Stand und bespre&shy;chen gemeinsames Vorgehen, um gesundheitliche Problematiken im Handlungsfeld Bewegung und Entspannung präventiv vorzu&shy;beugen. Ihre Mitarbeiter werden dadurch in festen monatlichen Intervallen sensibilisiert, dass Sie sich um das Wohlbefinden Ihrer Mitarbeiter kümmern und Sie auch darin investieren.</p>
    <p>Sie als Arbeitgeber können nicht wissen und auch zeitlich nicht ge&shy;währleisten welche individuellen gesundheitlichen Problematiken Ihre Mitarbeiter haben. Deshalb bieten wir Ihnen eine individuelle Lösung an Dienstleistung, welche den individuellen Bedarf Ihrer Mitarbeiter deckt.</p>
    <p>Ein Auszug aus unseren Leistun&shy;gen, damit Sie eine Vorstellung bekommen, was wir Ihnen und Ihren Mitarbeitern bieten können:</p>
  </div>

  <div class="col col--2">
    <div class="tag">Messung &amp; Analysen</div>
    <p>Messung &amp; Analysen zur indivi&shy;duellen <b>Stress- und Resilienz&shy;diagnostik</b> um zielorientiert ein <b>Streßmanagment</b> in Ihrem Betrieb zu implementieren.</p>
    <p><b>Dokumentation von Körperda&shy;ten und Risikofaktoren</b> in einer Einwgangskontrolle und einem ½ jährlichen Wiederholung der Kontrolle.</p>
    <p><b>Wirbelsäulen- und Haltungs&shy;screenings</b>, Haltung, Beweglich&shy;keit und Haltungskomponenten werden anschaulich dargestellt und bilden die Basis für zielfüh&shy;rende Visualisierung und fundier&shy;te Übungsempfehlung.</p>
    <p><b>Analysen von Körperstabilität und Gleichgewicht</b>; Balance Scan Pro ist ein erprobtes Analysetool für das Thema Körperstabilität</p>
    <div class="tag">Bewegungsprogramme</div>
    <p style="margin-bottom:0">Präventionsprogramme nach §20 zertifiziert von den Krankenkas&shy;sen wie zum Beispiel:</p>
    <ul class="plain-list">
      <li>Entspannungskurse Hatha Yoga</li>
      <li>- Pilates</li>
      <li>- Rückengymnastik</li>
      <li>- Ganzkörper Training an Geräten</li>
      <li>- Fit am Arbeitsplatz</li>
      <li>- Online-Präventionskurs (zeitlich und räumlich unabhängig)</li>
      <li>und einige mehr....</li>
    </ul>
  </div>

  <div class="col col--3">
    <div class="tag">Mentale Gesundheit</div>
    <p>Programme zur Achtsamkeit, Ent&shy;spannung, und Wahrnehmung. In Kleingruppen, Online oder als Einzelleistung buchbar</p>
    <ul class="bullets">
      <li>Digitaler Gesundheitscoach</li>
      <li>Workouts</li>
      <li>Live Online- Kurse</li>
      <li>Physio Übungen gezielt und individuell in der Einzelbera&shy;tung online und persönlich abgestimmt</li>
      <li>Online Präventionscoach</li>
      <li>Gesundheitstage für Firmen</li>
      <li>Individuell auf Ihre Firma ab&shy;gestimmt.</li>
    </ul>
    <div class="tag">Informationen zu den Kosten</div>
    <p><b>Bis zu 600 €</b> können Sie, als Arbeitgeber steuerfrei bezuschus&shy;sen. Voraussetzung dafür ist, dass die fachlichen Anforderungen des GKV- Spitzenverbandes erfüllt werden.</p>
    <p>Diese Leistungen können wir erfüllen und einige mehr on Top. Lassen Sie sich <b>persönlich</b> und <b>individuell</b> beraten und nehmen Sie <b>persönlich</b> oder <b>via E-Mail</b> Kontakt mit uns auf.</p>
  </div>

  <div class="footer-band"></div>
</section>

</body>
</html>
```